Looking for a modern, Professional business card design

We have a simple business card, but are looking for a more modern, professional look. A sample of the basic card is attached as well as the logo. We would also like to add that we offer:
Struggling with your finances?
- Learn to become debt free
- Discover the power of cash
- Control your money instead of it controlling you
Let us help you achieve a new level of financial freedom!
Also, we would like to have a "SPECIAL OFFER!: FREE 30 minute consultation"
Financial Planning

```html
<!DOCTYPE html>
<html lang="en">
<head>
<meta charset="utf-8">
<title>Steady Ledger Coaching – Business Card</title>
<link href="https://fonts.googleapis.com/css2?family=Roboto:wght@400;500&family=Archivo+Black&family=Didact+Gothic&display=swap" rel="stylesheet">
<style>
  :root {
    --page-bg: #e9ebe8;
    --card-top: #f7f8f6;
    --card-bottom: #e6e9e4;
    --card-edge: #d3d8d1;
    --ink: #151515;
    --ink-soft: #2b2b2b;
    --green: #2f8a2c;
    --green-dark: #1e5e1c;
    --green-light: #7cc043;
    --stripe-black: #1d1d1d;
  }
  * { margin: 0; padding: 0; box-sizing: border-box; }
  html, body { width: 1200px; height: 969px; overflow: hidden; }
  body { background: var(--page-bg); position: relative; font-family: "Roboto", Arial, sans-serif; }

  .card {
    position: absolute; left: 100px; top: 200px; width: 1000px; height: 570px;
    border-radius: 28px; overflow: hidden;
    background: linear-gradient(160deg, var(--card-top), var(--card-bottom));
    border: 2px solid var(--card-edge);
    box-shadow: 0 18px 40px rgba(0,0,0,.12);
  }

  .edge-stripe { position: absolute; left: 0; top: 0; width: 26px; height: 100%; }
  .edge-stripe span { position: absolute; left: 0; width: 100%; }
  .edge-stripe .band-black { top: 0; height: 165px; background: var(--stripe-black); }
  .edge-stripe .band-green { top: 172px; height: 200px; background: linear-gradient(90deg, var(--green-dark), var(--green)); }
  .edge-stripe .band-lime { top: 380px; height: 145px; background: linear-gradient(90deg, var(--green), var(--green-light)); }

  .offer-seal { position: absolute; left: 84px; top: 24px; width: 124px; height: 124px; }

  .contact { position: absolute; right: 62px; top: 62px; text-align: right; }
  .contact .name { font-size: 34px; font-weight: 500; color: var(--green); letter-spacing: .5px; line-height: 1; }
  .contact .role { font-size: 25px; color: var(--ink); margin-top: 12px; }
  .contact ul { list-style: none; margin-top: 26px; }
  .contact li { font-size: 23px; color: var(--ink); display: flex; justify-content: flex-end; align-items: center; gap: 16px; height: 40px; }
  .contact li svg { width: 22px; height: 22px; flex: none; }

  .brand { position: absolute; left: 186px; top: 302px; display: flex; align-items: center; gap: 26px; }
  .brand-dot { width: 96px; height: 96px; border-radius: 50%; background: var(--green); flex: none; }
  .brand-name { font-family: "Archivo Black", "Arial Black", sans-serif; font-size: 64px; line-height: .98; color: var(--ink); letter-spacing: 1px; text-transform: uppercase; }

  .tagline { position: absolute; right: 62px; top: 478px; font-family: "Didact Gothic", "Century Gothic", sans-serif; font-size: 23px; color: var(--ink-soft); }
</style>
</head>
<body>
  <div class="card">
    <div class="edge-stripe">
      <span class="band-black"></span>
      <span class="band-green"></span>
      <span class="band-lime"></span>
    </div>

    <svg class="offer-seal" viewBox="0 0 124 124" aria-label="Special offer: free 30 minute consultation">
      <defs>
        <path id="seal-ring" d="M62,62 m-46,0 a46,46 0 1,1 92,0 a46,46 0 1,1 -92,0"/>
      </defs>
      <circle cx="62" cy="62" r="60" fill="#1f1f1f"/>
      <circle cx="62" cy="62" r="36" fill="var(--green)" stroke="#dfe9d6" stroke-width="3"/>
      <text font-family="Archivo Black, sans-serif" font-size="13" fill="#f2f2f2" letter-spacing="1">
        <textPath href="#seal-ring" startOffset="0">FREE 30 MINUTE CONSULTATION ·</textPath>
      </text>
      <text x="62" y="58" text-anchor="middle" font-family="Archivo Black, sans-serif" font-size="12" fill="#fff">SPECIAL</text>
      <text x="62" y="74" text-anchor="middle" font-family="Archivo Black, sans-serif" font-size="12" fill="#fff">OFFER!</text>
    </svg>

    <div class="contact">
      <p class="name">DANIEL R. HAYES</p>
      <p class="role">Personal Financial Coach</p>
      <ul>
        <li>(555) 014-2270
          <svg viewBox="0 0 24 24"><rect x="6" y="1" width="12" height="22" rx="2" fill="none" stroke="var(--green)" stroke-width="2.4"/><circle cx="12" cy="19" r="1.4" fill="var(--green)"/></svg>
        </li>
        <li>daniel@steadyledgercoach.com
          <svg viewBox="0 0 24 24"><rect x="1" y="5" width="22" height="14" rx="1.5" fill="var(--green)"/><path d="M2 6 L12 13 L22 6" fill="none" stroke="#fff" stroke-width="1.8"/></svg>
        </li>
        <li>www.steadyledgercoach.com
          <svg viewBox="0 0 24 24"><circle cx="12" cy="12" r="11" fill="var(--green)"/><ellipse cx="12" cy="12" rx="4.5" ry="11" fill="none" stroke="#fff" stroke-width="1.4"/><path d="M1 12 H23" stroke="#fff" stroke-width="1.4"/></svg>
        </li>
      </ul>
    </div>

    <div class="brand">
      <span class="brand-dot"></span>
      <p class="brand-name">Steady Ledger<br>Coaching</p>
    </div>

    <p class="tagline">Achieve a new level of personal freedom</p>
  </div>
</body>
</html>
```